Corvane Paintless Dent Removal

Our company works on vehicles removing dents using a highly skilled trade which the metal is massaged out with special tools without disturbing the original paint, hence paintless dent removal. Besides keeping the paint and metal original its also very environmentally friendly since no paint or toxic fillers are used. Also we we are one of the most experienced companies in the business with 25 years

Target Market(s)

Retail Automobile consumers, Auto Dealerships and Auto Body Shops

Industry/Entity Type

Auto Repair

Contact Information for Business Card

Dale Hollister
PO Box 518 Brookmere, NY 11962
631-555-0148
corvanepdr@mailbox-example.com
website corvanepdr.example
youtube corvane paintless dent removal
25 years of experience removing Dents, Dings and Hail Damage

Font styles to use
Serif
Sans Serif

Colors

Designer to choose colors to be used in the design.

Requirements
Must have
• I do like things that are simple but classy and somewhat bold, also I like my logo so that should be somewhat important

```html
<!DOCTYPE html>
<html lang="en">
<head>
<meta charset="utf-8">
<title>Corvane Paintless Dent Removal – Business Card</title>
<link href="https://fonts.googleapis.com/css2?family=Roboto:wght@400;500&family=Roboto+Condensed:wght@700&display=swap" rel="stylesheet">
<style>
  :root {
    --navy: #1b2f5c;
    --navy-deep: #14244a;
    --green: #7cc242;
    --gold: #d9a520;
    --paper: #ffffff;
    --text-grey: #6b6f78;
    --backdrop: #e9e7e3;
  }
  * { margin: 0; padding: 0; box-sizing: border-box; }
  html, body { width: 1200px; height: 911px; overflow: hidden; }
  body {
    background: var(--backdrop);
    font-family: "Roboto", Arial, sans-serif;
    display: flex;
    flex-direction: column;
    align-items: center;
    justify-content: center;
    gap: 44px;
  }
  .card {
    position: relative;
    width: 620px;
    height: 354px;
    overflow: hidden;
    box-shadow: 0 6px 18px rgba(0,0,0,0.18);
  }

  /* Front */
  .card--front { background: var(--paper); }
  .name-band {
    position: absolute;
    top: 34px;
    right: 0;
    height: 58px;
    width: 300px;
    background: var(--navy);
    clip-path: polygon(14% 0, 100% 0, 100% 100%, 0 100%);
    display: flex;
    align-items: center;
    justify-content: flex-end;
    padding-right: 30px;
  }
  .name-band__text {
    font-family: "Roboto Condensed", "Arial Narrow", sans-serif;
    font-weight: 700;
    font-size: 24px;
    letter-spacing: 0.5px;
    color: #fff;
    text-transform: uppercase;
  }
  .brand {
    position: absolute;
    display: flex;
    align-items: center;
    gap: 14px;
  }
  .brand--front { left: 46px; top: 112px; }
  .brand__dot {
    width: 22px; height: 22px;
    border-radius: 50%;
    background: var(--green);
    flex-shrink: 0;
  }
  .brand__name {
    font-family: "Roboto Condensed", "Arial Narrow", sans-serif;
    font-weight: 700;
    line-height: 1.02;
    text-transform: uppercase;
  }
  .brand--front .brand__name { color: var(--navy); font-size: 34px; }
  .brand__name small { display: block; font-size: 0.5em; letter-spacing: 0.6px; }

  .contact {
    position: absolute;
    left: 46px;
    bottom: 30px;
    font-size: 13px;
    line-height: 1.55;
    color: var(--text-grey);
    list-style: none;
  }
  .contact__address { margin-bottom: 4px; }
  .contact__row { display: flex; align-items: center; gap: 8px; }
  .contact__icon {
    width: 13px; height: 13px;
    flex-shrink: 0;
    fill: var(--navy);
  }

  /* Back */
  .card--back { background: var(--navy); }
  .brand--back { left: 50px; top: 118px; }
  .brand--back .brand__dot { width: 30px; height: 30px; background: #fff; }
  .brand--back .brand__name { color: #fff; font-size: 46px; }
  .back-url {
    position: absolute;
    left: 94px;
    top: 232px;
    color: #fff;
    font-size: 16px;
    letter-spacing: 2px;
  }
  .years-badge {
    position: absolute;
    top: 26px;
    right: 28px;
    width: 62px; height: 62px;
    border-radius: 50%;
    background: var(--navy-deep);
    border: 3px solid var(--gold);
    display: flex;
    flex-direction: column;
    align-items: center;
    justify-content: center;
    color: var(--gold);
    font-family: "Roboto Condensed", "Arial Narrow", sans-serif;
    font-weight: 700;
    line-height: 1;
  }
  .years-badge__num { font-size: 22px; }
  .years-badge__label { font-size: 8px; letter-spacing: 1px; }
  .back-sweep {
    position: absolute;
    right: 0; bottom: 0;
    width: 220px; height: 70px;
    background: var(--navy-deep);
    clip-path: polygon(40% 100%, 100% 0, 100% 100%);
  }
</style>
</head>
<body>

<section class="card card--front" aria-label="Business card front">
  <div class="name-band"><span class="name-band__text">Dale Hollister</span></div>

  <div class="brand brand--front">
    <span class="brand__dot"></span>
    <p class="brand__name">Corvane<small>Paintless Dent Removal</small></p>
  </div>

  <ul class="contact">
    <li class="contact__address">PO Box 518<br>Brookmere, NY 11962</li>
    <li class="contact__row">
      <svg class="contact__icon" viewBox="0 0 24 24" aria-hidden="true"><path d="M6.6 10.8a15.1 15.1 0 0 0 6.6 6.6l2.2-2.2a1 1 0 0 1 1-.25 11.4 11.4 0 0 0 3.6.57 1 1 0 0 1 1 1V20a1 1 0 0 1-1 1A17 17 0 0 1 3 4a1 1 0 0 1 1-1h3.5a1 1 0 0 1 1 1c0 1.25.2 2.45.57 3.57a1 1 0 0 1-.25 1z"/></svg>
      631-555-0148
    </li>
    <li class="contact__row">
      <svg class="contact__icon" viewBox="0 0 24 24" aria-hidden="true"><path d="M2 5h20v14H2z M4 7v.5l8 5 8-5V7l-8 5z" fill-rule="evenodd"/></svg>
      corvanepdr@mailbox-example.com
    </li>
    <li class="contact__row">
      <svg class="contact__icon" viewBox="0 0 24 24" aria-hidden="true"><circle cx="12" cy="12" r="10" fill="none" stroke="currentColor" stroke-width="2" style="stroke:var(--navy)"/><path d="M2 12h20M12 2c3 3 3 17 0 20M12 2c-3 3-3 17 0 20" fill="none" style="stroke:var(--navy)" stroke-width="1.6"/></svg>
      corvanepdr.example
    </li>
    <li class="contact__row">
      <svg class="contact__icon" viewBox="0 0 24 24" aria-hidden="true"><rect x="3" y="3" width="18" height="18" rx="3"/></svg>
      corvane paintless dent removal
    </li>
  </ul>
</section>

<section class="card card--back" aria-label="Business card back">
  <div class="years-badge" aria-label="25 years of experience">
    <span class="years-badge__num">25</span>
    <span class="years-badge__label">YEARS</span>
  </div>

  <div class="brand brand--back">
    <span class="brand__dot"></span>
    <p class="brand__name">Corvane<small>Paintless Dent Removal</small></p>
  </div>
  <p class="back-url">corvanepdr.example</p>
  <div class="back-sweep"></div>
</section>

</body>
</html>
```